Cedarvale Ridge College

We are looking to update our current webpage at www.cedarvaleridge.ca. We would like to make it modern, fresh and appealing to students. We want to keep our logo the same with the logo colours blended in as the primary colours and focus. We are open to reconfiguring content as well.
Reason: Hi, In the next 3 days we will have narrowed our search to 3 designs and will make a choice before the final deadline...
College

```html
<!DOCTYPE html>
<html lang="en">
<head>
<meta charset="utf-8">
<title>Cedarvale Ridge College</title>
<link href="https://fonts.googleapis.com/css2?family=Roboto:ital,wght@0,400;0,500;0,700;1,400&family=Dancing+Script:wght@600&display=swap" rel="stylesheet">
<style>
:root{
  --green:#0b5c4e;
  --teal:#0f7d6c;
  --teal-dark:#0a5a4d;
  --footer:#0d5a4d;
  --footer-bar:#0a4f43;
  --footer-text:#e6f0ee;
  --tweet-link:#4fc3ad;
  --text:#666;
  --head:#333;
  --link:#0d6b5a;
  --white:#fff;
}
*{box-sizing:border-box;margin:0;padding:0}
html,body{width:708px;height:1200px;overflow:hidden;background:var(--white);font-family:"Roboto",Arial,sans-serif;color:var(--text)}
.page{position:relative;width:708px;height:1200px}
.abs{position:absolute}
.hero{left:0;top:0;width:708px;height:523px;background:linear-gradient(120deg,#d9dcc9 0%,#c8a892 30%,#b9856b 50%,#9aa884 70%,#e2e4da 100%)}
.topbar{left:83px;top:0;width:542px;height:20px;background:var(--green);color:var(--white);font-size:7px;display:flex;align-items:center;justify-content:space-between;padding:0 18px}
.topbar .right{display:flex;gap:18px;align-items:center}
.topbar svg{vertical-align:middle;margin-right:4px}
.header{left:83px;top:20px;width:542px;height:72px;background:var(--white)}
.brand{position:absolute;left:14px;top:18px;display:flex;align-items:center;gap:8px}
.brand-mark{width:14px;height:14px;border-radius:50%;background:var(--green)}
.brand-name{font-size:14px;font-weight:500;color:var(--green);line-height:1}
.tagline{position:absolute;left:178px;top:37px;font-family:"Dancing Script",cursive;font-size:13px;color:var(--green)}
.social{position:absolute;right:16px;top:31px;display:flex;gap:3px}
.social span{width:16px;height:16px;border-radius:50%;background:#c9c9c9}
.nav{left:83px;top:92px;width:542px;height:34px;background:var(--white);border-top:1px solid #e6e6e6;display:flex;box-shadow:0 1px 2px rgba(0,0,0,.15)}
.nav a{flex:1 1 auto;font-size:8px;color:#222;text-decoration:none;display:flex;align-items:center;justify-content:center;padding:0 6px;border-right:1px solid #e6e6e6;height:100%;white-space:nowrap}
.nav a.active{border-top:2px solid var(--green)}
.nav a:last-child{border-right:0}
.caption{left:85px;background:rgba(14,95,80,.82);color:var(--white);font-size:12px;padding:0 14px;height:33px;display:flex;align-items:center;letter-spacing:.2px}
.arrow{top:238px;width:23px;height:48px;background:rgba(255,255,255,.85);display:flex;align-items:center;justify-content:center}
.tiles{left:83px;top:478px;width:542px;height:94px;display:flex}
.tile{flex:1;display:flex;flex-direction:column;align-items:center;padding-top:13px;color:var(--white);font-size:9px}
.tile .ico{width:45px;height:45px;border-radius:50%;background:var(--white);display:flex;align-items:center;justify-content:center;margin-bottom:11px}
.t1{background:var(--teal-dark)}.t2{background:var(--teal)}.t3{background:var(--teal-dark)}.t4{background:var(--teal)}
.h2{font-size:11.5px;color:var(--head);letter-spacing:.2px}
.rule{height:0;border-bottom:1px dotted #bbb}
.photo-lead{left:83px;top:626px;width:116px;height:85px;background:linear-gradient(135deg,#5c4a42,#3a302d 60%,#7a6a60)}
.welcome-lead{left:218px;top:627px;font-size:7px;font-style:italic;color:var(--link)}
.welcome-text{left:218px;top:640px;width:407px;font-size:6.6px;line-height:13.2px}
.btn{left:218px;top:697px;width:40px;height:17px;background:var(--green);color:var(--white);font-size:7px;display:flex;align-items:center;justify-content:center}
.video{left:83px;top:770px;width:214px;height:120px;background:linear-gradient(180deg,#d8d5cc,#a99583 60%,#6b5a4f)}
.video-bar{left:83px;top:770px;width:214px;height:9px;background:#111}
.video-ctrl{left:83px;top:882px;width:214px;height:8px;background:#111}
.video-prog{left:83px;top:880px;width:47px;height:2px;background:#d00}
.play{left:177px;top:817px;width:22px;height:22px;background:#111;border-radius:3px;display:flex;align-items:center;justify-content:center}
.video-text{left:83px;top:901px;width:214px;font-size:6.6px;line-height:10.6px;text-align:justify}
.news{left:334px;width:291px;display:flex;gap:10px}
.news .thumb{width:67px;height:50px;border:2px solid #eee;flex:none}
.news h3{font-size:7.8px;font-weight:400;color:var(--link);margin-top:1px}
.news .date{font-size:6.4px;font-style:italic;color:#aaa;margin-top:2px}
.news p{font-size:6.4px;line-height:10px;margin-top:1px}
.footer{left:0;top:974px;width:708px;height:226px;background:var(--footer)}
.fcol{top:992px;font-size:6.8px;color:var(--footer-text)}
.fcol h4{font-size:9px;font-weight:700;color:var(--white);margin-bottom:10px}
.fcol p{line-height:13px}
.fdiv{top:990px;width:0;height:138px;border-left:1px solid rgba(255,255,255,.12)}
.flist{list-style:none}
.flist li{line-height:16.6px;display:flex;align-items:center;gap:6px}
.flist li::before{content:"";border-left:3px solid var(--footer-text);border-top:2.5px solid transparent;border-bottom:2.5px solid transparent}
.tweet{display:flex;gap:8px;line-height:13px;margin-bottom:14px}
.tweet em{font-style:normal;color:var(--tweet-link)}
.contact-row{display:flex;gap:8px;line-height:13px;align-items:flex-start}
.contact-row svg{margin-top:3px;flex:none}
.bottombar{left:70px;top:1155px;width:542px;height:45px;background:var(--footer-bar);color:var(--white);font-size:7px;display:flex;align-items:center;justify-content:space-between;padding:0 24px 0 23px}
</style>
</head>
<body>
<div class="page">
  <div class="abs hero" role="img" aria-label="Photo of students writing at desks in a classroom"></div>

  <div class="abs topbar">
    <span>Map &amp; Directions &nbsp;/&nbsp; Campus Map &nbsp;/&nbsp; Photo Tour</span>
    <span class="right">
      <span><svg width="7" height="7" viewBox="0 0 10 10"><path d="M2 0l2 2-1 2 3 3 2-1 2 2-2 2C4 10 0 6 0 2z" fill="#fff"/></svg>(604) 555-0182</span>
      <span><svg width="7" height="5" viewBox="0 0 10 7"><rect width="10" height="7" fill="#fff"/><path d="M0 0l5 4 5-4" stroke="#0b5c4e" fill="none"/></svg>info@cedarvaleridge.ca</span>
    </span>
  </div>

  <div class="abs header">
    <div class="brand"><span class="brand-mark"></span><span class="brand-name">Cedarvale Ridge<br>College</span></div>
    <div class="tagline">learn. grow. serve</div>
    <div class="social"><span></span><span></span><span></span><span></span></div>
  </div>

  <nav class="abs nav">
    <a class="active">Home</a><a>About Us</a><a>Contact Us</a><a>Consider Cedarvale</a><a>Current Students</a><a>Alumni</a><a>Supporters</a><a>News + Events</a><a>Ridge Park</a>
  </nav>

  <div class="abs caption" style="top:228px">LOREM IPSUM DOLOR SIT AMET CONSECTE</div>
  <div class="abs caption" style="top:262px">ADIPISCING ELIT AENEAN COMMO</div>

  <div class="abs arrow" style="left:0;border-right:2px solid var(--green)"><svg width="7" height="12" viewBox="0 0 7 12"><path d="M6 1L1 6l5 5" stroke="#0b5c4e" stroke-width="1.4" fill="none"/></svg></div>
  <div class="abs arrow" style="right:0;border-left:2px solid var(--green)"><svg width="7" height="12" viewBox="0 0 7 12"><path d="M1 1l5 5-5 5" stroke="#0b5c4e" stroke-width="1.4" fill="none"/></svg></div>

  <div class="abs tiles">
    <div class="tile t1"><span class="ico"><svg width="18" height="20" viewBox="0 0 18 20"><rect x="1" y="2" width="13" height="17" rx="1" fill="#0b5c4e"/><rect x="4" y="0" width="7" height="4" fill="#0b5c4e"/><path d="M4 8h7M4 11h7M4 14h4" stroke="#fff"/><circle cx="14" cy="15" r="4" fill="#0b5c4e" stroke="#fff"/><path d="M12 15l1.5 1.5L16 13.5" stroke="#fff" fill="none"/></svg></span>APPLY TODAY</div>
    <div class="tile t2"><span class="ico"><svg width="22" height="20" viewBox="0 0 22 20"><text x="9" y="9" font-size="10" font-family="Roboto,sans-serif" font-weight="700" fill="#0b5c4e">$</text><path d="M1 13h5l4 2h6c2 0 2 2 0 2h-6M1 13v6h4l6-1 9-4" stroke="#0b5c4e" stroke-width="1.6" fill="none"/></svg></span>DONATE</div>
    <div class="tile t3"><span class="ico"><svg width="22" height="16" viewBox="0 0 22 16"><path d="M11 3C8 1 4 1 1 2v13c3-1 7-1 10 1 3-2 7-2 10-1V2c-3-1-7-1-10 1zM11 3v13" stroke="#0b5c4e" stroke-width="1.5" fill="none"/></svg></span>LIBRARY</div>
    <div class="tile t4"><span class="ico"><svg width="16" height="20" viewBox="0 0 16 20"><rect x="1" y="1" width="14" height="18" rx="1" stroke="#0b5c4e" stroke-width="1.5" fill="none"/><path d="M4 5h8M4 8h8M4 11h8M4 14h6" stroke="#0b5c4e"/></svg></span>TEXT FOR INFO</div>
  </div>

  <div class="abs h2" style="left:83px;top:595px">WELCOME TO CEDARVALE RIDGE COLLEGE</div>
  <div class="abs rule" style="left:83px;top:613px;width:542px"></div>
  <div class="abs photo-lead" role="img" aria-label="Portrait of the college president speaking"></div>
  <div class="abs welcome-lead">Thank-you for your interest in Cedarvale Ridge College!</div>
  <p class="abs welcome-text">I hope that your visit here will answer some of your questions as you consider a course of study that is right for you. Whether you are interested in pastoral ministry, counselling, missions and cross-cultural communication, theology, worship arts, music or our one-year Foundations year you'll discover we've designed programs that will equip you to excel in your chosen calling. Two of our newest programs are Community Service Leadership, and Digital Arts &amp; Media Studies. For those of you that are looking to transition ...</p>
  <div class="abs btn">More</div>

  <div class="abs h2" style="left:83px;top:733px">LATEST VIDEOS</div>
  <div class="abs rule" style="left:83px;top:751px;width:223px"></div>
  <div class="abs h2" style="left:334px;top:733px">NEWS &amp; EVENTS</div>
  <div class="abs rule" style="left:334px;top:751px;width:291px"></div>

  <div class="abs video" role="img" aria-label="Video still of a lecturer teaching a class of raised-hand students"></div>
  <div class="abs video-bar"></div>
  <div class="abs video-ctrl"></div>
  <div class="abs video-prog"></div>
  <div class="abs play"><svg width="8" height="9" viewBox="0 0 8 9"><path d="M0 0l8 4.5L0 9z" fill="#fff"/></svg></div>
  <p class="abs video-text">Lorem ipsum dolor sit amet, consectetuer adipiscing elit. Aenean commodo ligula eget dolor. Aenean massa.Cum sociis natoque penatibus et magnis dis parturient montes, nascetur ridiculus mus. Donec quam felis, ultricies nec.</p>

  <div class="abs news" style="top:770px"><div class="thumb" role="img" aria-label="Group of smiling students holding books" style="background:linear-gradient(135deg,#c9d4dc,#d89a6a 55%,#6b8aa8)"></div><div><h3>Lorem ipsum dolor sit amet, consectetuer adipiscing elit.</h3><div class="date">Posted On 21/11/2014</div><p>Aenean commodo ligula eget dolor. Aenean massa. Cum sociis natoque penatibus et magnis dis parturient montes.</p></div></div>
  <div class="abs news" style="top:832px"><div class="thumb" role="img" aria-label="Student with books in front of a chalkboard" style="background:linear-gradient(135deg,#e8e4de,#c99b84 50%,#3a3d3c)"></div><div><h3>Lorem ipsum dolor sit amet, consectetuer adipiscing elit.</h3><div class="date">Posted On 21/11/2014</div><p>Aenean commodo ligula eget dolor. Aenean massa. Cum sociis natoque penatibus et magnis dis parturient montes.</p></div></div>
  <div class="abs news" style="top:895px"><div class="thumb" role="img" aria-label="Students working together at a table" style="background:linear-gradient(135deg,#9bb4c8,#c98f6c 50%,#e2ddd2)"></div><div><h3>Lorem ipsum dolor sit amet, consectetuer adipiscing elit.</h3><div class="date">Posted On 21/11/2014</div><p>Aenean commodo ligula eget dolor. Aenean massa. Cum sociis natoque penatibus et magnis dis parturient montes.</p></div></div>

  <footer class="abs footer"></footer>
  <div class="abs fdiv" style="left:208px"></div>
  <div class="abs fdiv" style="left:380px"></div>
  <div class="abs fdiv" style="left:538px"></div>

  <div class="abs fcol" style="left:83px;width:112px">
    <h4>Contact Us</h4>
    <p>Fusce dapibus, tellus condimentum utellus fermalsuada magna. Fusce dapibus, tellus magna.</p>
    <div style="height:12px"></div>
    <div class="contact-row"><svg width="6" height="8" viewBox="0 0 6 8"><path d="M3 0a3 3 0 00-3 3c0 2 3 5 3 5s3-3 3-5a3 3 0 00-3-3z" fill="#fff"/></svg><span>4810 Ridgeline Road • PO Box 220 • Hillcrest • BC • CANADA • V0X 1A0</span></div>
    <div class="contact-row"><svg width="6" height="8" viewBox="0 0 10 10"><path d="M2 0l2 2-1 2 3 3 2-1 2 2-2 2C4 10 0 6 0 2z" fill="#fff"/></svg><span>(604) 555-0182</span></div>
    <div class="contact-row"><svg width="6" height="8" viewBox="0 0 10 10"><rect y="2" width="10" height="7" fill="#fff"/><path d="M0 2l5 4 5-4" stroke="#0d5a4d" fill="none"/></svg><span>info@cedarvaleridge.ca</span></div>
  </div>

  <div class="abs fcol" style="left:227px;width:140px">
    <h4>Latest Tweets</h4>
    <div class="tweet"><span>▸</span><span>Aenean lacinia bibendum nulla sed leo posuere erat a ante venenatis dapibus <em>posuere velit aliquet.</em></span></div>
    <div class="tweet"><span>▸</span><span>Donec ullamcorper metus auctor fringilla. Nullam <em>quis risus eget.</em></span></div>
    <div class="tweet"><span>▸</span><span><em>Vestibulum id ligula</em> porta euismod semper. Maecenas faucibus mollis.</span></div>
  </div>

  <div class="abs fcol" style="left:402px;width:130px">
    <h4>Admissions</h4>
    <ul class="flist"><li>Download the full Catalogue</li><li>Apply Today (Application Package)</li><li>Information Request</li><li>Browse our Programs</li><li>Download Forms</li><li>Admissions Information</li><li>Campus Directory</li></ul>
  </div>

  <div class="abs fcol" style="left:566px;width:100px">
    <h4>Admissions</h4>
    <ul class="flist"><li>Home</li><li>About Us</li><li>Consider Cedarvale</li><li>Current Students</li><li>Alumni</li><li>Supporters</li><li>News + Events</li></ul>
  </div>

  <div class="abs bottombar"><span>© 2014 Copyright - cedarvaleridge - All Rights Reserved</span><span>Top &nbsp;⌃</span></div>
</div>
</body>
</html>
```